Business Intelligence Application - Reporting Menu and Report Criteria Design

Looking for a fresh, effective and user friendly view for the menu structure and reporting criteria screen format for a business reporting application. Initial format completed, content structure is in place, but we need the 'wow' design.. as its a serious professional report/BI tool it has to fall within certain guidelines for clarity and graphics..but we want it to be slick, friendly, great user experience. There is a large amount of complex content to fit into a small space and we need it to be very inviting, modern and intuitive.. If interested, please review the attachment. We have live screens in operation, but feel these could be improved and looking forward to seeing what great creative suggestions could be made. Please review work done to date in the attached.. We are not looking for a total re-design of everything, all the basic business content/structure is there.. but tell us what we could do to improve this in terms of graphic design... particularly the criteria screens.. thanks!
Updates

Reason: Need a few more days to review designs - thanks for all submissions so far, we will make a selection shortly.

Target Market(s)

Business analysts, hotel operations teams, finance analysts hospitality industry

Industry/Entity Type

Hospitality

Coding

Coded - Design and coding required

Number of Pages Required

4 page

Font styles to use
Sans Serif
Other font styles liked:
• Candara, please see example in deck

Colors
3276b5
3176b5
0255a3
85acd3
33a6d7
cee9f5
85cae6

Requirements
Must have
• sharp clear, logical menu structure, (currently it has 'clicks to sub-menus, we need hover over, slide to sub-menus..) colour, styling.. and most focus on revision of criteria.. right now is somewhat heavy, cumbersome.. keep colour and friendly intuitive process steps.. its heavy analytical stuff.. best of luck!
Should not have
• No grey fonts on white or grey screens! many business apps are not readable or sharp.. or fonts are too small.. colourless, so please avoid that.. see our deck - sharp dark (navy) or black fonts on white, or light shading..

```html
<!DOCTYPE html>
<html lang="en">
<head>
<meta charset="utf-8">
<title>Yield Desk – Property Search</title>
<link rel="stylesheet" href="https://fonts.googleapis.com/css2?family=Mulish:wght@400;600;700;800&display=swap">
<style>
  :root{
    --navy:#021736;
    --brand-blue:#0255a3;
    --tab-active:#2f92d0;
    --tab-light:#52b2de;
    --body-top:#3f9fd8;
    --body-bottom:#0b62b2;
    --panel:#55b5e0;
    --menu:#2c8fcd;
    --menu-line:#5aaee0;
    --field:#ffffff;
    --field-shade:#ececec;
    --option-grey:#dedede;
    --text-dark:#3a4656;
    --white:#ffffff;
    --accent-cyan:#2ee0e8;
    --footer:#e3e3e3;
    --footer-text:#4a4a4a;
  }
  *{box-sizing:border-box;margin:0;padding:0}
  html,body{width:1200px;height:664px;overflow:hidden}
  body{position:relative;font-family:"Mulish",sans-serif;color:var(--white);background:var(--body-bottom)}

  .topbar{position:absolute;left:0;top:0;width:1200px;height:113px;background:var(--navy)}
  .brand{position:absolute;left:97px;top:40px;display:flex;align-items:center;gap:18px}
  .brand-mark{width:30px;height:30px;border-radius:50%;background:var(--accent-cyan)}
  .brand-name{font-size:28px;font-weight:700;color:var(--white);letter-spacing:.2px}
  .user{position:absolute;left:781px;top:34px;display:flex;align-items:center;gap:8px}
  .avatar{width:44px;height:44px;border-radius:50%;background:radial-gradient(circle at 50% 40%,#c9b6a6,#6d6258)}
  .user-text{font-size:15px;line-height:21px}
  .user-text strong{font-weight:700}
  .bar-divider{position:absolute;top:38px;width:1px;height:40px;background:#1d3357}
  .top-icon{position:absolute;top:43px}

  .nav{position:absolute;left:0;top:113px;width:1200px;height:51px;background:var(--brand-blue)}
  .nav-item{position:absolute;top:0;height:51px;display:flex;align-items:center;gap:8px;font-size:18px;font-weight:600;color:var(--white)}
  .nav-item svg{flex:none}
  .nav-item--admin{left:85px;width:129px;padding-left:22px;background:var(--tab-active)}
  .nav-item--management{left:214px;width:191px;padding-left:28px}
  .nav-item--search{left:405px;width:229px;padding-left:45px;background:var(--tab-light)}
  .nav-item--intel{left:634px;width:133px;padding-left:35px}
  .nav-item--planning{left:767px;padding-left:23px;border-left:1px solid #3d85c9}

  .stage{position:absolute;left:0;top:164px;width:1200px;height:424px;background:linear-gradient(180deg,var(--body-top),var(--body-bottom))}
  .criteria{position:absolute;left:112px;top:183px;width:974px;height:320px;background:var(--panel)}
  .label{position:absolute;font-size:17px;font-weight:700;letter-spacing:.2px;color:var(--white)}
  .label--plain{font-size:18px;font-weight:600;letter-spacing:0}
  .field{position:absolute;height:43px;background:linear-gradient(180deg,var(--field),var(--field-shade));border:1px solid #d4d4d4}
  .select svg{position:absolute;right:14px;top:16px}
  .option{position:absolute;height:43px;display:flex;align-items:center;padding-left:20px;font-size:16px;color:var(--text-dark);border:1px solid #d2d2d2}
  .option--current{background:linear-gradient(180deg,#fff,#efefef)}
  .option--muted{background:var(--option-grey)}
  .option--hover{background:var(--tab-light);color:var(--white);border-color:#7cc6e8}
  .search-btn{position:absolute;left:820px;top:416px;width:215px;height:51px;background:var(--brand-blue);border:none;color:var(--white);font-family:inherit;font-size:20px;font-weight:700;letter-spacing:.5px}

  .menu{position:absolute;left:84px;top:164px;width:266px;height:173px;background:var(--menu);box-shadow:2px 4px 8px rgba(0,40,90,.25)}
  .menu-item{position:absolute;left:0;width:266px;height:37px;display:flex;align-items:center;padding-left:32px;font-size:16px;font-weight:600;color:var(--white);border-bottom:1px solid var(--menu-line)}
  .menu-item--active{width:475px;background:var(--brand-blue);border-bottom:none}
  .submenu{position:absolute;left:350px;top:245px;width:209px;height:258px;background:var(--brand-blue);padding:20px 0 0 31px;list-style:none;box-shadow:2px 4px 8px rgba(0,30,70,.3)}
  .submenu li{font-size:14px;font-weight:600;line-height:28px;color:var(--white)}

  .footer{position:absolute;left:0;top:588px;width:1200px;height:76px;background:var(--footer);display:flex;align-items:center;justify-content:center;font-size:13px;color:var(--footer-text)}
</style>
</head>
<body>
  <header class="topbar">
    <div class="brand">
      <span class="brand-mark"></span>
      <span class="brand-name">Yield Desk</span>
    </div>
    <div class="user">
      <div class="avatar" role="img" aria-label="Portrait photo of the signed-in administrator"></div>
      <div class="user-text">Welcome<br><strong>Admin</strong></div>
    </div>
    <span class="bar-divider" style="left:919px"></span>
    <svg class="top-icon" style="left:947px" width="28" height="28" viewBox="0 0 24 24" aria-label="Notifications"><path fill="#2a8fd6" d="M12 2a2 2 0 0 1 2 2v.6A6.5 6.5 0 0 1 18.5 11v5l2 2.5H3.5l2-2.5v-5A6.5 6.5 0 0 1 10 4.6V4a2 2 0 0 1 2-2zm-2.5 18h5a2.5 2.5 0 0 1-5 0z"/></svg>
    <span class="bar-divider" style="left:1005px"></span>
    <svg class="top-icon" style="left:1034px" width="30" height="26" viewBox="0 0 24 20" aria-label="Sign out"><path fill="#2a8fd6" d="M14 0l9 8-9 8v-5C7 11 3 13 0 19c1-8 5-13 14-14z"/></svg>
  </header>

  <nav class="nav">
    <div class="nav-item nav-item--admin">
      <svg width="22" height="22" viewBox="0 0 24 24"><circle cx="12" cy="7" r="5" fill="#fff"/><path fill="#fff" d="M2 23c0-6 4.5-9 10-9s10 3 10 9z"/></svg>Admin
    </div>
    <div class="nav-item nav-item--management">
      <svg width="28" height="24" viewBox="0 0 28 24"><g fill="#fff"><rect x="10" y="0" width="8" height="7"/><rect x="0" y="17" width="8" height="7"/><rect x="10" y="17" width="8" height="7"/><rect x="20" y="17" width="8" height="7"/><rect x="13" y="7" width="2" height="10"/><rect x="3" y="11" width="22" height="2"/><rect x="3" y="11" width="2" height="6"/><rect x="23" y="11" width="2" height="6"/></g></svg>Management
    </div>
    <div class="nav-item nav-item--search">
      <svg width="20" height="20" viewBox="0 0 24 24"><circle cx="10" cy="10" r="7" fill="none" stroke="#fff" stroke-width="3"/><path d="M15 15l7 7" stroke="#fff" stroke-width="3.5" stroke-linecap="round"/></svg>Property Search
    </div>
    <div class="nav-item nav-item--intel">
      <svg width="22" height="22" viewBox="0 0 24 24"><circle cx="12" cy="12" r="11" fill="#fff"/><path fill="#0255a3" d="M7 5c2 1 3 3 2 5s-3 2-3 4-2 1-3 0c0-4 2-7 4-9zm8 3c2 0 4 2 3 5s-3 6-5 6c0-2 1-3 0-5s0-6 2-6z"/></svg>Intel
    </div>
    <div class="nav-item nav-item--planning">
      <svg width="22" height="22" viewBox="0 0 24 24"><path fill="#fff" d="M10 1h4l.6 3 2.4 1 2.6-1.7 2.8 2.8L20.7 8.7l1 2.4 3 .6v4l-3 .6-1 2.4 1.7 2.6-2.8 2.8-2.6-1.7-2.4 1-.6 3h-4l-.6-3-2.4-1-2.6 1.7-2.8-2.8 1.7-2.6-1-2.4-3-.6v-4l3-.6 1-2.4L1.6 5.1 4.4 2.3 7 4l2.4-1z" transform="scale(.92) translate(1 0)"/><circle cx="12" cy="12" r="4" fill="#0255a3"/></svg>Planning
    </div>
  </nav>

  <main class="stage"></main>

  <section class="criteria-area" aria-label="Property search criteria">
    <div class="criteria"></div>

    <span class="label" style="left:460px;top:227px">SEARCH ID</span>
    <div class="field" style="left:460px;top:257px;width:278px"></div>
    <span class="label" style="left:753px;top:227px">SEARCH PRODUCT</span>
    <div class="field" style="left:751px;top:257px;width:283px"></div>

    <span class="label" style="left:158px;top:326px">DIVISIONS</span>
    <span class="label label--plain" style="left:460px;top:326px">Regions</span>
    <span class="label label--plain" style="left:751px;top:326px">Areas</span>

    <div class="option option--current" style="left:157px;top:358px;width:240px">North America</div>
    <div class="option option--current" style="left:157px;top:401px;width:240px">Southwest USA</div>
    <div class="option option--muted" style="left:157px;top:440px;width:240px">Northwest USA</div>

    <div class="field select" style="left:460px;top:358px;width:278px">
      <svg width="24" height="12" viewBox="0 0 24 12"><path d="M1 1l11 10L23 1" fill="none" stroke="#8a8a8a" stroke-width="2"/></svg>
    </div>
    <div class="field select" style="left:751px;top:358px;width:283px">
      <svg width="24" height="12" viewBox="0 0 24 12"><path d="M1 1l11 10L23 1" fill="none" stroke="#8a8a8a" stroke-width="2"/></svg>
    </div>

    <div class="option option--current" style="left:440px;top:440px;width:282px;padding-left:28px">Chicago Hotel</div>
    <div class="option option--hover" style="left:440px;top:483px;width:282px;padding-left:28px">New York Hotel</div>

    <button class="search-btn" type="button">SEARCH</button>
  </section>

  <div class="menu" aria-label="Admin menu">
    <div class="menu-item" style="top:8px">Registration</div>
    <div class="menu-item" style="top:45px">User Access</div>
    <div class="menu-item menu-item--active" style="top:82px;left:-1px">Setup</div>
    <div class="menu-item" style="top:120px;border-bottom:none">Data Imports</div>
  </div>
  <ul class="submenu" aria-label="Setup submenu">
    <li>Market Segments</li>
    <li>Banquet &amp; Catering</li>
    <li>Outlets/F&amp;B Service</li>
    <li>Other Income</li>
    <li>Impact Dates</li>
    <li>Inventory</li>
    <li>Geo/Location</li>
    <li>Distribution Channels</li>
  </ul>

  <footer class="footer">© 2017 Company Name&nbsp; All right reserved&nbsp; Term of Use</footer>
</body>
</html>
```